Business Card for Professional Photographer

I'm looking for an eye catching modern clean design that compliments my logo/ website fonts & colours.
I specialise in architecture, corporate & commercial photography so I'm marketing to professional clients rather than portrait / wedding clients.

I would prefer to not have a solid black design.

My logo brand guide is as follows :

Main front font. : Reislust
Main font colour : #fff
Slogan front font : Ubuntu Bold
Monogram front font : Venti Medium
Container colour : #fff

I need print ready files in pdf .png & .eps formats.

Included in the files below are some screen grabs as reference to font & colours etc.

```html
<!DOCTYPE html>
<html lang="en">
<head>
<meta charset="utf-8">
<title>North Light Studio – Business Card</title>
<link rel="stylesheet" href="https://fonts.googleapis.com/css2?family=Raleway:wght@400&family=Ubuntu:wght@400;700&family=Roboto:wght@400&family=Exo+2:wght@700&display=swap">
<style>
  :root {
    --backdrop: #3a3a3a;
    --card: #1c1c1e;
    --card-deep: #141416;
    --gold: #d4a94a;
    --gold-light: #ecc96d;
    --text: #f2f2f2;
    --photo-a: #2b2c30;
    --photo-b: #1f2024;
    --photo-c: #34312c;
  }
  * { box-sizing: border-box; margin: 0; padding: 0; }
  html, body { width: 799px; height: 1200px; overflow: hidden; }
  body {
    background: var(--backdrop);
    display: flex;
    flex-direction: column;
    align-items: center;
    justify-content: center;
    gap: 90px;
    font-family: "Roboto", sans-serif;
  }
  .card {
    position: relative;
    width: 680px;
    height: 390px;
    border-radius: 4px;
    overflow: hidden;
    background: var(--card);
    box-shadow: 0 14px 30px rgba(0,0,0,.45);
  }

  /* Front */
  .card-front .collage {
    position: absolute; inset: 0;
    display: grid;
    grid-template-columns: 1.2fr 1fr 1.4fr;
    grid-template-rows: 1fr 1fr;
    gap: 3px;
    background: var(--card-deep);
  }
  .collage .tile:nth-child(1) { background: linear-gradient(160deg, var(--photo-a), var(--photo-b)); grid-row: span 2; }
  .collage .tile:nth-child(2) { background: linear-gradient(200deg, var(--photo-c), var(--photo-b)); }
  .collage .tile:nth-child(3) { background: linear-gradient(140deg, #2e3138, var(--photo-b)); grid-row: span 2; }
  .collage .tile:nth-child(4) { background: linear-gradient(180deg, var(--photo-b), var(--photo-c)); }
  .card-front .shade {
    position: absolute; inset: 0;
    background: rgba(10,10,12,.35);
  }
  .front-brand {
    position: absolute;
    left: 60px; top: 130px;
    display: flex; align-items: center; gap: 22px;
  }
  .brand-dot {
    width: 22px; height: 22px;
    background: var(--gold);
    border-radius: 50%;
    flex: none;
  }
  .brand-name {
    font-family: "Raleway", sans-serif;
    font-weight: 400;
    color: var(--gold);
    letter-spacing: 4px;
    text-transform: uppercase;
    font-size: 30px;
    line-height: 1;
  }
  .brand-tagline {
    font-family: "Ubuntu", sans-serif;
    font-weight: 700;
    color: var(--gold);
    font-size: 13px;
    letter-spacing: 2px;
    margin-top: 8px;
  }
  .front-web {
    position: absolute;
    left: 104px; top: 278px;
    font-family: "Raleway", sans-serif;
    color: var(--gold-light);
    font-size: 17px;
    letter-spacing: 3px;
  }

  /* Back */
  .card-back {
    background: linear-gradient(135deg, #232325, var(--card) 60%, #18181a);
  }
  .back-brand {
    position: absolute;
    left: 40px; top: 34px;
  }
  .back-brand .brand-name { font-size: 24px; letter-spacing: 5px; }
  .back-brand .brand-tagline { font-size: 11px; margin-top: 6px; }
  .person {
    position: absolute;
    left: 40px; top: 128px;
  }
  .person-name {
    font-family: "Exo 2", sans-serif;
    font-weight: 700;
    color: var(--gold);
    font-size: 20px;
  }
  .person-role { color: var(--text); font-size: 15px; margin-top: 2px; }
  .contacts {
    position: absolute;
    left: 40px; top: 200px;
    list-style: none;
    color: var(--text);
    font-size: 15px;
    line-height: 24px;
  }
  .contacts li { display: flex; align-items: center; gap: 10px; }
  .contacts svg { width: 14px; height: 14px; fill: var(--gold); flex: none; }
  .back-mark {
    position: absolute;
    right: 40px; bottom: 48px;
    text-align: right;
  }
  .back-mark .brand-name {
    font-size: 34px;
    letter-spacing: 5px;
    line-height: 1.25;
  }
</style>
</head>
<body>

  <section class="card card-front" aria-label="Card front">
    <div class="collage" role="img" aria-label="Darkened collage of architecture and commercial photographs">
      <div class="tile"></div><div class="tile"></div><div class="tile"></div><div class="tile"></div>
    </div>
    <div class="shade"></div>
    <div class="front-brand">
      <span class="brand-dot"></span>
      <div>
        <div class="brand-name">North Light Studio</div>
        <div class="brand-tagline">Architecture Corporate Commercial</div>
      </div>
    </div>
    <div class="front-web">www.northlightstudio.com.au</div>
  </section>

  <section class="card card-back" aria-label="Card back">
    <div class="back-brand">
      <div class="brand-name">North Light Studio</div>
      <div class="brand-tagline">Architecture Corporate Commercial</div>
    </div>
    <div class="person">
      <div class="person-name">Tom Harlow</div>
      <div class="person-role">Photographer</div>
    </div>
    <ul class="contacts">
      <li><svg viewBox="0 0 16 16" aria-hidden="true"><path d="M3 1h3l1.5 4-2 1.2a9 9 0 0 0 4.3 4.3L11 8.5l4 1.5v3a2 2 0 0 1-2 2A12 12 0 0 1 1 3a2 2 0 0 1 2-2z"/></svg>0400123456</li>
      <li><svg viewBox="0 0 16 16" aria-hidden="true"><path d="M1 3h14v10H1z M1 3l7 6 7-6" stroke="#1c1c1e" stroke-width="1.2"/></svg>info@northlightstudio.com.au</li>
      <li><svg viewBox="0 0 16 16" aria-hidden="true"><circle cx="8" cy="8" r="7"/><path d="M1 8h14M8 1c-3 3-3 11 0 14M8 1c3 3 3 11 0 14" stroke="#1c1c1e" stroke-width="1" fill="none"/></svg>www.northlightstudio.com.au</li>
      <li>8 Harbour Rd Lakeside Vic 3000</li>
    </ul>
    <div class="back-mark">
      <div class="brand-name">North Light<br>Studio</div>
    </div>
  </section>

</body>
</html>
```